Velmo Swinger site - new website, blogsite and merchandise point, connection to tradeva

We are a well established Swingers Club in the North east of UK and already have an existing site. www.velmo-example.co.uk, BUT we have changed our logo and our information on the site needs to be updated.

We are changing our hosting site to Nimbrashost.example ,also wanting to start a blog which is linked to the club, plus we wish to sell a small exclusive range of Velmo linked merchandise which will also be available on Tradeva.

I have attached a pdf of the majority of the content. additionally we will provide pictures and a videoclip which should be able to be viewed by pc's, lap tops and mobile phones (the whole website must be fully accessible via phone).

The new site must be able to be updated by someone with medium computer knowledge (usually me), by no means expert. Updates will generally be new pictures and written information. The site must be able to be transferred to NimbrasHost.

Velmo is one of the countries leading clubs and emphasises friendliness, fun & safety for its members, we look after you to ensure your experience is the best we can offer. We are very proud of our reputation, built up over more than 10 years.

Target Market(s)

Swingers, dreamers & fantasists, alternative lifestyle people

Coding

Coded - Design and coding required

Number of Pages Required

5+ page

Font styles to use
Sans Serif

Colors
000000
ec1f27
fbfbfb
eeeeee
eaeaea

Requirements
Must have
• website with blog attached, link to tradeva & quidlo, ability to run videoclip and picture album and must be compatable to transfer easily to Nimbrashost and be updated by non-professional (who can learn)
• Straightforward & easy to navigate
• over 18 content page with enter button
Nice to have
• sexy site
• link to chirpster maybe
• black site would be nice with red or white writing
Should not have
• children and animals in anyway shape or form

```html
<!DOCTYPE html>
<html lang="en">
<head>
<meta charset="utf-8">
<title>Velmo – Home</title>
<link rel="stylesheet" href="https://fonts.googleapis.com/css2?family=Playfair+Display:ital,wght@0,400;0,700;1,400&family=Open+Sans:wght@400;600&display=swap">
<style>
:root{
  --black:#000000;
  --red:#ec1f27;
  --white:#fbfbfb;
  --light:#eeeeee;
  --pale:#eaeaea;
  --line:#b3141a;
  --serif:'Playfair Display', Georgia, serif;
  --sans:'Open Sans', Arial, sans-serif;
}
*{box-sizing:border-box;margin:0;padding:0}
html,body{width:667px;height:1200px;overflow:hidden;background:var(--black)}
body{position:relative;font-family:var(--sans);color:var(--white)}
a{color:inherit;text-decoration:none}
ul{list-style:none}

/* Header */
.top-bar{position:absolute;top:0;left:0;width:667px;height:44px;background:var(--black);border-bottom:1px solid var(--line);z-index:3}
.brand{position:absolute;left:58px;top:5px;font-family:var(--serif);font-size:28px;font-weight:400;letter-spacing:1px;color:var(--white);line-height:32px}
.contact-strip{position:absolute;right:72px;top:19px;display:flex;gap:17px;font-size:8px;color:var(--white)}
.contact-strip span{display:flex;align-items:center;gap:7px}
.contact-strip svg{width:8px;height:8px;fill:var(--white)}

.main-nav{position:absolute;top:45px;left:0;width:667px;height:30px;border-bottom:1px solid var(--line);background:rgba(0,0,0,.55);z-index:3}
.main-nav ul{display:flex;justify-content:center;gap:17px;padding-top:8px;padding-left:25px}
.main-nav a{font-family:var(--serif);font-size:8.4px;color:var(--white)}

/* Hero */
.hero{position:absolute;top:45px;left:0;width:667px;height:291px;background:
 linear-gradient(180deg,rgba(10,6,4,.55) 0%,rgba(10,6,4,0) 30%,rgba(10,6,4,0) 70%,rgba(10,6,4,.6) 100%),
 linear-gradient(100deg,#2a1a10 0%,#6b4a30 22%,#8a6848 45%,#6e4e36 65%,#3e2a1c 85%,#1e130c 100%)}
.hero-title{position:absolute;top:155px;width:100%;text-align:center}
.hero-title .welcome{font-family:var(--serif);font-style:italic;font-size:13px;color:var(--white)}
.hero-title .hero-brand{font-family:var(--serif);font-size:30px;font-weight:400;letter-spacing:1px;color:var(--white);margin-top:4px}
.scroll-tab{position:absolute;left:319px;top:336px;width:28px;height:14px;z-index:3}

/* About + Blog */
.dark-band{position:absolute;top:336px;left:0;width:667px;height:361px;background:
 radial-gradient(circle at 8% 20%,rgba(120,20,25,.45) 0,rgba(0,0,0,0) 80px),
 radial-gradient(circle at 90% 45%,rgba(90,20,30,.45) 0,rgba(0,0,0,0) 90px),
 radial-gradient(circle at 30% 70%,rgba(110,30,30,.35) 0,rgba(0,0,0,0) 110px),
 radial-gradient(circle at 75% 90%,rgba(40,50,90,.35) 0,rgba(0,0,0,0) 90px),
 linear-gradient(180deg,#1a0608,#0b0304)}
.section-heading{display:flex;align-items:center;justify-content:center;gap:16px;font-family:var(--serif);font-weight:700;color:var(--white)}
.section-heading::before,.section-heading::after{content:"";height:1px;width:100px;background:rgba(255,255,255,.45)}
.about .section-heading{position:absolute;top:30px;width:100%;font-size:13px}
.about p{position:absolute;top:58px;left:88px;width:491px;text-align:center;font-size:7.2px;line-height:14.3px}
.btn{display:inline-block;background:var(--red);color:var(--white);font-family:var(--serif);font-weight:700;font-size:7.2px;border-radius:10px;text-align:center;line-height:19px}
.about .btn{position:absolute;top:127px;left:303px;width:61px}
.blog .section-heading{position:absolute;top:158px;width:100%;font-size:13px}
.blog .section-heading::before,.blog .section-heading::after{width:90px}
.blog-grid{position:absolute;top:187px;left:78px;display:flex;gap:20px}
.blog-card{width:158px}
.blog-card .thumb{width:158px;height:79px}
.blog-card p{font-size:6.1px;line-height:11.5px;text-align:center;margin-top:7px;padding:0 2px}
.blog .btn{position:absolute;top:321px;left:288px;width:91px}

/* Products */
.products{position:absolute;top:697px;left:0;width:667px;height:303px;background:var(--red)}
.products .section-heading{position:absolute;top:19px;width:100%;font-size:13.5px}
.products .section-heading::before,.products .section-heading::after{background:rgba(255,255,255,.6);width:95px}
.product-grid{position:absolute;top:56px;left:108px;display:flex;gap:23px}
.product-card{width:135px}
.product-card .shot{position:relative;width:135px;height:185px;background:var(--white)}
.product-card .meta{display:flex;justify-content:space-between;align-items:baseline;padding:9px 12px 0 2px;font-family:var(--serif);font-weight:700}
.product-card .name{font-size:9px}
.product-card .price{font-size:12px}
.partner-badge{position:absolute;left:34px;top:93px;width:61px;height:28px;border-radius:4px;background:#1b1b1b}

/* Footer */
.site-footer{position:absolute;top:1000px;left:0;width:667px;height:200px;background:var(--black)}
.footer-title{font-family:var(--serif);font-weight:700;font-size:12px;color:var(--red)}
.quick-links{position:absolute;left:81px;top:16px}
.quick-links ul{margin-top:9px}
.quick-links li{font-size:6.6px;line-height:14.3px;display:flex;align-items:center;gap:11px}
.quick-links li svg{width:5px;height:6px}
.events{position:absolute;left:245px;top:16px}
.events ul{margin-top:10px}
.events li{display:flex;gap:9px;margin-bottom:12px}
.events .thumb{width:35px;height:31px;flex:none}
.events p{font-size:6.6px;line-height:11.4px;width:105px}
.footer-contact{position:absolute;left:451px;top:18px}
.footer-contact ul{margin-top:8px}
.footer-contact li{font-size:6.8px;line-height:14.3px;display:flex;align-items:center;gap:10px}
.footer-contact li svg{width:7px;height:7px;fill:var(--white)}
.follow{margin-top:13px}
.social{display:flex;gap:5px;margin-top:8px}
.social span{width:17px;height:17px;border-radius:3px}
.copyright{font-size:5.6px;margin-top:14px;color:var(--white)}
</style>
</head>
<body>

<header class="top-bar">
  <a class="brand" href="#">VELMO</a>
  <div class="contact-strip">
    <span><svg viewBox="0 0 10 10"><path d="M2 0.5l2 2-1 1.3c.6 1.3 1.5 2.2 2.8 2.8l1.2-1 2 2-1.3 1.6C4 8.7 1.3 6 .4 1.9z"/></svg>0790 0100234</span>
    <span><svg viewBox="0 0 10 10"><path d="M0 2h10v6H0z M1 3v.3l4 2.5 4-2.5V3z" fill-rule="evenodd"/></svg>velmoswingers@mailbox.example</span>
  </div>
</header>

<nav class="main-nav">
  <ul>
    <li><a href="#">Home</a></li>
    <li><a href="#">Diary</a></li>
    <li><a href="#">Theme Parties</a></li>
    <li><a href="#">TV/TG and Admirers</a></li>
    <li><a href="#">Membership</a></li>
    <li><a href="#">FAQs</a></li>
    <li><a href="#">Rooms</a></li>
    <li><a href="#">Contact Us</a></li>
    <li><a href="#">Links</a></li>
  </ul>
</nav>

<section class="hero" role="img" aria-label="Photo of a group of friends celebrating with gold balloons and sparklers at a party">
  <div class="hero-title">
    <div class="welcome">Welcome</div>
    <div class="hero-brand">VELMO</div>
  </div>
</section>
<svg class="scroll-tab" viewBox="0 0 28 14" aria-hidden="true">
  <path d="M0 0h28l-6 14H6z" fill="#3a3a3a"/>
  <path d="M10.5 4.5l3.5 3.5 3.5-3.5" stroke="#fbfbfb" stroke-width="1.6" fill="none"/>
</svg>

<main class="dark-band">
  <section class="about">
    <h2 class="section-heading">About Velmo</h2>
    <p>We are the best Swingers Club in the North East, and also voted No 2 club in the UK.<br>
    We have retained the coveted title of No 1 friendliest club in the UK (in joint 1st place with our great friends "Open Door Social", London).<br>
    This prestigious award has been given to us by a panel of "mystery voters" (swingers, singles &amp; couples) working with the publication called "Nights in the Cities" a copy of which is available in reception.</p>
    <a class="btn" href="#">Read more</a>
  </section>

  <section class="blog">
    <h2 class="section-heading">Blog</h2>
    <div class="blog-grid">
      <article class="blog-card">
        <div class="thumb" role="img" aria-label="Photo of a crowd dancing under colourful club lights" style="background:linear-gradient(120deg,#2a3fb0 0%,#6a2a9a 40%,#b0205a 75%,#3b0f40 100%)"></div>
        <p>Theme party attire is getting more and more popular now, but whichever you chose, vanilla or the theme suggested, you will not feel out of place.</p>
      </article>
      <article class="blog-card">
        <div class="thumb" role="img" aria-label="Photo of well dressed couples chatting at the bar" style="background:linear-gradient(120deg,#2a1f18 0%,#6e5240 45%,#a08470 70%,#2a1e16 100%)"></div>
        <p>We have a prize for the best dressed couple or single (judged by our bar staff)....</p>
      </article>
      <article class="blog-card">
        <div class="thumb" role="img" aria-label="Photo of dancers performing on stage" style="background:linear-gradient(120deg,#5a4038 0%,#8c7064 45%,#6a5450 70%,#2a2224 100%)"></div>
        <p>On theme party nights we have a Buffet so you can nibble away......</p>
      </article>
    </div>
    <a class="btn" href="#">View More Blog</a>
  </section>
</main>

<section class="products">
  <h2 class="section-heading">Top Products</h2>
  <div class="product-grid">
    <article class="product-card">
      <div class="shot" role="img" aria-label="Photo of a model wearing the white Velmo T-shirt and black trousers" style="background:linear-gradient(180deg,#f4f4f4 0%,#eaeaea 35%,#f2f2f2 68%,#3a3a3a 80%,#1c1c1c 100%)">
        <span class="partner-badge" aria-hidden="true"></span>
      </div>
      <div class="meta"><span class="name">Velmo T-shirt</span><span class="price">$54</span></div>
    </article>
    <article class="product-card">
      <div class="shot" role="img" aria-label="Photo of a gold and amber hookah with a brown hose" style="background:linear-gradient(180deg,#fbfbfb 0%,#f6e8c4 30%,#f0d48a 62%,#e9bf4e 78%,#fbfbfb 100%)"></div>
      <div class="meta"><span class="name">Hookah</span><span class="price">$54</span></div>
    </article>
    <article class="product-card">
      <div class="shot" role="img" aria-label="Photo of a dark beer bottle beside a full glass of dark beer" style="background:linear-gradient(180deg,#fbfbfb 0%,#d8d2cc 18%,#4a403a 45%,#2a2320 80%,#fbfbfb 100%)"></div>
      <div class="meta"><span class="name">Beer</span><span class="price">$54</span></div>
    </article>
  </div>
</section>

<footer class="site-footer">
  <div class="quick-links">
    <h3 class="footer-title">Quick Links</h3>
    <ul>
      <li><svg viewBox="0 0 5 6"><path d="M1 .5l2.5 2.5L1 5.5" stroke="#fbfbfb" fill="none"/></svg>Home</li>
      <li><svg viewBox="0 0 5 6"><path d="M1 .5l2.5 2.5L1 5.5" stroke="#fbfbfb" fill="none"/></svg>Diary</li>
      <li><svg viewBox="0 0 5 6"><path d="M1 .5l2.5 2.5L1 5.5" stroke="#fbfbfb" fill="none"/></svg>Theme Parties</li>
      <li><svg viewBox="0 0 5 6"><path d="M1 .5l2.5 2.5L1 5.5" stroke="#fbfbfb" fill="none"/></svg>TV/TG and Admirers</li>
      <li><svg viewBox="0 0 5 6"><path d="M1 .5l2.5 2.5L1 5.5" stroke="#fbfbfb" fill="none"/></svg>Membership</li>
      <li><svg viewBox="0 0 5 6"><path d="M1 .5l2.5 2.5L1 5.5" stroke="#fbfbfb" fill="none"/></svg>FAQs</li>
      <li><svg viewBox="0 0 5 6"><path d="M1 .5l2.5 2.5L1 5.5" stroke="#fbfbfb" fill="none"/></svg>Rooms</li>
      <li><svg viewBox="0 0 5 6"><path d="M1 .5l2.5 2.5L1 5.5" stroke="#fbfbfb" fill="none"/></svg>Contact Us</li>
      <li><svg viewBox="0 0 5 6"><path d="M1 .5l2.5 2.5L1 5.5" stroke="#fbfbfb" fill="none"/></svg>Links</li>
    </ul>
  </div>

  <div class="events">
    <h3 class="footer-title">Events</h3>
    <ul>
      <li><div class="thumb" role="img" aria-label="Photo of a DJ deck" style="background:linear-gradient(135deg,#1c2a4a,#6a3a70)"></div><p>Sed ut perspiciatis unde omnis iste natus error sit voluptatem accusantium</p></li>
      <li><div class="thumb" role="img" aria-label="Photo of a party crowd" style="background:linear-gradient(135deg,#6a2a5a,#c08030)"></div><p>Sed ut perspiciatis unde omnis iste natus error sit voluptatem accusantium</p></li>
      <li><div class="thumb" role="img" aria-label="Photo of dancers under blue lights" style="background:linear-gradient(135deg,#1a3a8a,#8a2a6a)"></div><p>Sed ut perspiciatis unde omnis iste natus error sit voluptatem accusantium</p></li>
    </ul>
  </div>

  <div class="footer-contact">
    <h3 class="footer-title">Contact Us</h3>
    <ul>
      <li><svg viewBox="0 0 10 10"><path d="M2 0.5l2 2-1 1.3c.6 1.3 1.5 2.2 2.8 2.8l1.2-1 2 2-1.3 1.6C4 8.7 1.3 6 .4 1.9z"/></svg>Phone: 07900 100234</li>
      <li><svg viewBox="0 0 10 10"><path d="M0 2h10v6H0z M1 3v.3l4 2.5 4-2.5V3z" fill-rule="evenodd"/></svg>Email: velmoswingers@mailbox.example</li>
      <li><svg viewBox="0 0 10 10"><circle cx="5" cy="5" r="4.5"/></svg>Website: VelmoNights.example</li>
    </ul>
    <h3 class="footer-title follow">Follow Us</h3>
    <div class="social">
      <span style="background:#3b5a9a"></span>
      <span style="background:#2a9ad0"></span>
      <span style="background:#d0504a"></span>
      <span style="background:#2a7ab0"></span>
    </div>
    <p class="copyright">Copyright© 2017. All Rights Reserved.</p>
  </div>
</footer>

</body>
</html>
```